4 Poster Designs required for Nail Salon

We require 4 poster designs that will be displayed inside a shopping centre. Each design should contain our logo and the words "Located next to Tallmart" (or similar). Design 1 (MOTHERS DAY) should contain the words "Mothers Day Special" and "$10 gift voucher when you spend over $50". Design 2 (CHRISTMAS) should contain the words "Christmas in July" and "Purchase a set of nails and get a $10 gift voucher". Design 3 (ALL YEAR) should contain the words "New Deluxe Spa Pedicure Service" and the words "Try our new Deluxe Spa Pedicure and get a free nail buff, shape and polish for your fingernails". Design 4 (ALL YEAR 2)should contain high quality nail salon image(s) and the words "Now Open". We like designs that support our image of high quality/fun/clean and safe.
Updates
I will close this early. In 24 hours.
Target Market(s)
Rich mums
Industry/Entity Type
Shopping
Look and feel
Each slider illustrates characteristics of the customer's brand and the style your logo design should communicate.

```html
<!DOCTYPE html>
<html lang="en">
<head>
<meta charset="utf-8">
<title>Deluxe Spa Pedicure Poster</title>
<link rel="stylesheet" href="https://fonts.googleapis.com/css2?family=Great+Vibes&family=Poppins:wght@300;600&display=swap">
<style>
  :root {
    --backdrop: #e8e8e6;
    --paper: #ffffff;
    --script-pink: #e17fb5;
    --ink: #3a3a3c;
    --brand-pink-deep: #dc4f98;
    --brand-pink-light: #eb8fc0;
    --logo-white: #ffffff;
    --skin-light: #f6e2d8;
    --skin-mid: #e8bfae;
    --tulip: #f2a7c6;
  }
  html, body {
    margin: 0;
    padding: 0;
    width: 1200px;
    height: 1148px;
    overflow: hidden;
    background: var(--backdrop);
  }
  .poster {
    position: absolute;
    left: 226px;
    top: 24px;
    width: 748px;
    height: 1100px;
    background: var(--paper);
    overflow: hidden;
    box-shadow: 0 2px 10px rgba(0,0,0,0.08);
  }
  .hero-photo {
    position: absolute;
    left: 82px;
    top: 0;
    width: 555px;
    height: 370px;
    background:
      radial-gradient(ellipse at 8% 62%, var(--tulip) 0 7%, transparent 14%),
      radial-gradient(ellipse at 92% 60%, var(--tulip) 0 7%, transparent 14%),
      radial-gradient(ellipse at 50% 45%, var(--skin-mid) 0%, var(--skin-light) 45%, var(--paper) 78%);
  }
  .headline {
    position: absolute;
    left: 60px;
    top: 400px;
    width: 680px;
    margin: 0;
    font-family: "Great Vibes", cursive;
    font-weight: 400;
    font-size: 108px;
    line-height: 104px;
    color: var(--script-pink);
    transform: rotate(-8deg);
    transform-origin: left top;
  }
  .headline span { display: block; }
  .headline .line-two { padding-left: 30px; }
  .offer {
    position: absolute;
    left: 419px;
    top: 680px;
    margin: 0;
    font-family: "Poppins", sans-serif;
    font-weight: 600;
    font-size: 19px;
    line-height: 26px;
    letter-spacing: 0.2px;
    text-transform: uppercase;
    color: var(--ink);
  }
  .brand-panel {
    position: absolute;
    left: 389px;
    top: 792px;
    width: 359px;
    height: 205px;
    background: linear-gradient(90deg, var(--brand-pink-deep), var(--brand-pink-light));
  }
  .brand-name {
    position: absolute;
    left: 58px;
    top: 58px;
    margin: 0;
    font-family: "Poppins", sans-serif;
    font-weight: 300;
    font-size: 48px;
    line-height: 52px;
    letter-spacing: 3px;
    color: var(--logo-white);
  }
  .brand-descriptor {
    position: absolute;
    right: 34px;
    top: 116px;
    margin: 0;
    font-family: "Poppins", sans-serif;
    font-weight: 300;
    font-size: 16px;
    letter-spacing: 1px;
    color: var(--logo-white);
  }
  .location {
    position: absolute;
    left: 389px;
    top: 1018px;
    width: 359px;
    margin: 0;
    text-align: center;
    font-family: "Poppins", sans-serif;
    font-weight: 300;
    font-size: 15px;
    letter-spacing: 3px;
    text-transform: uppercase;
    color: var(--ink);
  }
  .location strong { font-weight: 600; }
</style>
</head>
<body>
  <main class="poster">
    <div class="hero-photo" role="img" aria-label="Photo of manicured hands resting on pedicured feet with French tip nails, flanked by pink tulips"></div>

    <h1 class="headline">
      <span class="line-one">New Deluxe Spa</span>
      <span class="line-two">Pedicure Service</span>
    </h1>

    <p class="offer">Try our new deluxe spa<br>pedicure and get a free<br>nail buff, shape and polish<br>for your fingernails</p>

    <div class="brand-panel">
      <p class="brand-name">Whisper</p>
      <p class="brand-descriptor">Nail Salon</p>
    </div>

    <p class="location">Located next to <strong>Tallmart</strong></p>
  </main>
</body>
</html>
```